Business Card Design for BrightvaleMedia.com

--I need a business card design for my company BrightvaleMedia.com

I have attached my logo...I want the brightvale media logo on the front of the business card, and then I want The Quillstone Chief on the back of it with my information.

I would like to see a light colored background as well as a dark colored background

FRONT:
BRIGHTVALE MEDIA LOGO
248 N. Larkmoor
3rd Floor
San Diego CA 92173
www.BrightvaleMedia.com

Advanced Website & App Development
Websites, Apps, Online Voucher Systems

Leading Edge Marketing Services
SMS, VB, SMM, SEM,

BACK:
QUILLSTONE CHIEF LOGO
Dorian Pelletta
The Quillstone Chief
Call Or Text: 619-555-0148
Dorian@QuillstoneChief.example
www.QuillstoneChief.example

Target Market(s)

small business owners

Industry/Entity Type

Business Consultant

Contact Information for Business Card

FRONT:
BRIGHTVALE MEDIA LOGO
248 N. Larkmoor
3rd Floor
San Diego CA 92173
www.BrightvaleMedia.com

SMS, VB, SMM, SEM,

BACK:
QUILLSTONE CHIEF LOGO
Dorian Pelletta
The Quillstone Chief
Dorian@QuillstoneChief.example
www.QuillstoneChief.example

Requirements
Must have
• add this quote on it somewhere, anywhere,preferrably on back
• "The Fastest Way To Success Is To Take Action”
• — Dorian Pelletta, Quillstone Chief
Nice to have
• open
Should not have
• red

```html
<!DOCTYPE html>
<html lang="en">
<head>
<meta charset="utf-8">
<title>Brightvale Media – Business Cards</title>
<link href="https://fonts.googleapis.com/css2?family=Roboto+Condensed:ital,wght@0,300;0,400;0,700;1,400&display=swap" rel="stylesheet">
<style>
  :root {
    --page-bg: #e9e7e3;
    --card-white: #f7f7f7;
    --brand-blue: #1296c4;
    --brand-blue-deep: #0a7fae;
    --band-grey: #9a9c9f;
    --text-light: #ffffff;
    --rule-light: rgba(255,255,255,0.75);
    --rule-grey: #9a9c9f;
  }
  * { box-sizing: border-box; margin: 0; padding: 0; }
  html, body { width: 1200px; height: 780px; overflow: hidden; }
  body {
    background: var(--page-bg);
    font-family: "Roboto Condensed", Arial, sans-serif;
    position: relative;
  }
  .card {
    position: absolute;
    width: 540px;
    height: 310px;
    border-radius: 16px;
    overflow: hidden;
    background: var(--card-white);
    box-shadow: 0 6px 18px rgba(0,0,0,0.18);
  }
  .card--chief { left: 40px; top: 235px; }
  .card--media { left: 620px; top: 235px; }
  .card__shapes { position: absolute; inset: 0; width: 100%; height: 100%; }

  .wordmark {
    position: absolute;
    color: var(--brand-blue);
    font-weight: 400;
    text-transform: uppercase;
    white-space: nowrap;
    line-height: 1;
  }
  .card--chief .wordmark { left: 28px; top: 58px; font-size: 24px; letter-spacing: 2px; }

  .site-link {
    position: absolute;
    color: var(--text-light);
    font-size: 14px;
    font-weight: 400;
    white-space: nowrap;
  }
  .card--chief .site-link { right: 22px; top: 20px; }

  .quote {
    position: absolute;
    left: 284px;
    top: 70px;
    width: 234px;
    color: var(--text-light);
    font-size: 13px;
    line-height: 1.35;
  }
  .quote__text { font-style: italic; }
  .quote__by { margin-top: 4px; font-size: 12px; opacity: 0.9; }

  .person { position: absolute; left: 236px; top: 188px; color: var(--text-light); }
  .person__name { font-size: 22px; font-weight: 700; letter-spacing: 0.5px; line-height: 1; white-space: nowrap; }
  .person__title { font-size: 14px; font-weight: 400; margin-top: 3px; }
  .person__contact { margin-top: 12px; font-size: 14px; line-height: 1.35; white-space: nowrap; }

  .card--media .wordmark { right: 22px; top: 52px; font-size: 24px; letter-spacing: 2px; }
  .wordmark-rule {
    position: absolute; right: 22px; top: 90px;
    width: 226px; height: 1px; background: var(--rule-grey);
  }
  .services { position: absolute; left: 24px; top: 46px; color: var(--text-light); font-size: 13.5px; line-height: 1.35; white-space: nowrap; }
  .services__lead { font-weight: 700; margin-top: 6px; }
  .services__rule { position: absolute; left: 24px; top: 176px; width: 266px; height: 1px; background: var(--rule-light); }
  .address { position: absolute; left: 24px; top: 192px; color: var(--text-light); font-size: 13.5px; line-height: 1.5; white-space: nowrap; }
</style>
</head>
<body>

  <section class="card card--chief" aria-label="Quillstone Chief card">
    <svg class="card__shapes" viewBox="0 0 540 310" preserveAspectRatio="none" aria-hidden="true">
      <defs>
        <linearGradient id="chiefBlue" x1="0" y1="0" x2="1" y2="1">
          <stop offset="0" stop-color="#18a3d1"/>
          <stop offset="1" stop-color="#0a7fae"/>
        </linearGradient>
      </defs>
      <path d="M300 0 C288 108 168 196 62 310 L540 310 L540 0 Z" fill="var(--band-grey)"/>
      <path d="M322 0 C310 110 190 200 86 310 L540 310 L540 0 Z" fill="url(#chiefBlue)"/>
    </svg>
    <div class="wordmark">Quillstone Chief</div>
    <div class="site-link">www.QuillstoneChief.example</div>
    <blockquote class="quote">
      <p class="quote__text">“The Fastest Way To Success Is To Take Action”</p>
      <p class="quote__by">— Dorian Pelletta, Quillstone Chief</p>
    </blockquote>
    <div class="person">
      <div class="person__name">DORIAN PELLETTA</div>
      <div class="person__title">The Quillstone Chief</div>
      <div class="person__contact">
        <div>Call Or Text: 619-555-0148</div>
        <div>Email: Dorian@QuillstoneChief.example</div>
      </div>
    </div>
  </section>

  <section class="card card--media" aria-label="Brightvale Media card">
    <svg class="card__shapes" viewBox="0 0 540 310" preserveAspectRatio="none" aria-hidden="true">
      <defs>
        <linearGradient id="mediaBlue" x1="0" y1="0" x2="1" y2="1">
          <stop offset="0" stop-color="#0a7fae"/>
          <stop offset="1" stop-color="#18a3d1"/>
        </linearGradient>
      </defs>
      <path d="M0 0 L232 0 C262 120 318 214 450 310 L0 310 Z" fill="url(#mediaBlue)"/>
    </svg>
    <div class="wordmark">Brightvale Media</div>
    <div class="wordmark-rule"></div>
    <div class="services">
      <div>Advanced Website &amp; App Development</div>
      <div>Websites, Apps, Online Voucher Systems</div>
      <div class="services__lead">Leading Edge Marketing Services</div>
      <div>SMS | VB | SMM | SEM</div>
    </div>
    <div class="services__rule"></div>
    <div class="address">
      <div>248 N. Larkmoor , 3rd Floor , San Diego CA 92173</div>
      <div>www.BrightvaleMedia.com</div>
    </div>
  </section>

</body>
</html>
```